Card design for orthopaedic surgeons working as The Brightwater Joint Centre

Business cards, letterhead

Colors

Designer to choose colors to be used in the design.

Requirements
Must have
• Late addition.
• Cards letterhead must have logos of
• Crestmoor Lindell College of Surgeons
• Varenwood Bone Health Association
Nice to have
• Back of card to have space for appointment time to be added by hand and some blank space for writing incidental other notes.

```html
<!DOCTYPE html>
<html lang="en">
<head>
<meta charset="utf-8">
<title>The Brightwater Joint Centre – Business Card</title>
<link href="https://fonts.googleapis.com/css2?family=Poppins:wght@300;400;500&display=swap" rel="stylesheet">
<style>
  :root {
    --page-bg: #e4ddd4;
    --card-light: #eceae6;
    --card-dark: #0f3a47;
    --wave-teal: #3f8ea3;
    --wave-gold: #c9aa84;
    --name-teal: #4fa0b6;
    --text-light: #d9dedf;
    --text-warm: #c7ad8e;
  }
  * { margin: 0; padding: 0; box-sizing: border-box; }
  html, body { width: 1200px; height: 1047px; overflow: hidden; }
  body {
    background: var(--page-bg);
    font-family: "Poppins", sans-serif;
    position: relative;
  }
  .business-card {
    position: absolute;
    left: 100px; top: 251px;
    width: 1000px; height: 545px;
    border-radius: 22px;
    overflow: hidden;
    background: var(--card-light);
    box-shadow: 0 10px 30px rgba(0,0,0,0.12);
  }
  .card-wave { position: absolute; inset: 0; width: 100%; height: 100%; }
  .brand-name {
    position: absolute; left: 40px; top: 124px;
    font-size: 26px; font-weight: 400; letter-spacing: 0.5px;
    color: var(--card-dark);
  }
  .holder { position: absolute; right: 40px; top: 250px; text-align: right; }
  .holder-name {
    font-size: 35px; font-weight: 400; letter-spacing: 2px;
    color: var(--name-teal); line-height: 1.2;
  }
  .holder-title {
    font-size: 22px; font-weight: 400; letter-spacing: 1px;
    color: var(--text-light); margin-top: 2px;
  }
  .holder-rule {
    width: 104px; height: 1px; background: var(--text-light);
    opacity: 0.7; margin: 20px 0 0 auto;
  }
  .contact-list {
    position: absolute; right: 40px; top: 372px;
    list-style: none; text-align: right;
  }
  .contact-list li {
    display: flex; align-items: center; justify-content: flex-end;
    gap: 14px;
    font-size: 23px; letter-spacing: 1.2px; line-height: 35px;
    color: var(--text-light);
  }
  .contact-list svg { width: 16px; height: 16px; flex: none; }
  .address {
    position: absolute; left: 40px; top: 443px;
    font-size: 23px; letter-spacing: 1.2px; line-height: 35px;
    color: var(--text-warm);
    font-style: normal;
  }
</style>
</head>
<body>
  <section class="business-card">
    <svg class="card-wave" viewBox="0 0 1000 545" preserveAspectRatio="none" aria-hidden="true">
      <path d="M0,262 C210,330 400,300 610,232 C790,176 910,182 1000,252 L1000,545 L0,545 Z" fill="var(--card-dark)"/>
      <path d="M0,248 C210,318 400,290 610,222 C790,166 910,172 1000,242" fill="none" stroke="var(--wave-teal)" stroke-width="12"/>
      <path d="M0,260 C210,328 400,298 610,230 C790,174 910,180 1000,250" fill="none" stroke="var(--wave-gold)" stroke-width="3"/>
    </svg>

    <div class="brand-name">The Brightwater Joint Centre</div>

    <div class="holder">
      <div class="holder-name">DANIEL HARROW</div>
      <div class="holder-title">Director</div>
      <div class="holder-rule"></div>
    </div>

    <ul class="contact-list">
      <li>555-318-4720
        <svg viewBox="0 0 16 16"><path d="M4 1.5l2.2 3-1.3 1.6c.8 1.8 2.2 3.2 4 4l1.6-1.3 3 2.2-1 2.3C7.6 13.3 2.7 8.4 2 3z" fill="none" stroke="var(--name-teal)" stroke-width="1.3" stroke-linejoin="round"/></svg>
      </li>
      <li>555-642-0193
        <svg viewBox="0 0 16 16"><rect x="4" y="1" width="8" height="14" rx="1.5" fill="none" stroke="var(--name-teal)" stroke-width="1.3"/><circle cx="8" cy="12.4" r="0.9" fill="var(--name-teal)"/></svg>
      </li>
      <li>info@brightwaterjoint.com
        <svg viewBox="0 0 16 16"><rect x="1.5" y="3.5" width="13" height="9" rx="1" fill="none" stroke="var(--name-teal)" stroke-width="1.3"/><path d="M1.8 4l6.2 4.8L14.2 4" fill="none" stroke="var(--name-teal)" stroke-width="1.3"/></svg>
      </li>
      <li>www.brightwaterjoint.com
        <svg viewBox="0 0 16 16"><circle cx="8" cy="8" r="6.3" fill="none" stroke="var(--name-teal)" stroke-width="1.2"/><ellipse cx="8" cy="8" rx="2.7" ry="6.3" fill="none" stroke="var(--name-teal)" stroke-width="1.1"/><path d="M1.7 8h12.6M2.7 5h10.6M2.7 11h10.6" stroke="var(--name-teal)" stroke-width="1"/></svg>
      </li>
    </ul>

    <address class="address">
      48 Calloway Street<br>
      Ashford, TN 37140
    </address>
  </section>
</body>
</html>
```